Kesso Tea Premium Matcha brand Label

This is a label design project for a luxury tea brand. Feel free to be creative within the guidelines.
Attached to this project is a document called “Private Label Design Requirements” with the design guidelines and template. There is another document called "Kesso Tea Packaging Instructions" this has more details necessary to stick to the guidelines in the first document.

I have also attached the certifications to be included as well as different variations of the logo for you to use.

If you have any questions, I am here.
Updates

Need extra days to review

Target Market(s)

Young, active, fun, enjoy the finer things

```html
<!DOCTYPE html>
<html lang="en">
<head>
<meta charset="utf-8">
<title>Kesso Tea – Premium Organic Ceremonial Matcha Label</title>
<link rel="stylesheet" href="https://fonts.googleapis.com/css2?family=Montserrat:wght@300;400;500;600;700&display=swap">
<style>
  :root {
    --matcha: #72bf4a;
    --ink: #050505;
    --paper: #f7f7f7;
    --white: #ffffff;
    --badge-green: #3d9a3a;
    --badge-blue: #2b6fb3;
    --badge-brown: #7a4a2a;
  }
  * { box-sizing: border-box; margin: 0; padding: 0; }
  html, body {
    width: 1200px; height: 996px; overflow: hidden;
    background: var(--white);
    font-family: "Montserrat", Arial, sans-serif;
  }
  .canvas { position: relative; width: 1200px; height: 996px; }

  .label {
    position: absolute; left: 50px; top: 406px;
    width: 1100px; height: 183px;
    background: var(--ink);
    box-shadow: 0 10px 28px rgba(0,0,0,.18);
  }
  .label__top {
    position: absolute; left: 0; top: 0; width: 100%; height: 93px;
    background: var(--paper);
  }

  .brand-mark {
    position: absolute; left: 18px; top: 30px;
    display: flex; align-items: center; gap: 6px;
    font-weight: 600; font-size: 14px; color: var(--ink);
  }
  .brand-mark__dot { width: 10px; height: 10px; border-radius: 50%; background: var(--matcha); }

  .origin { position: absolute; left: 16px; top: 108px; color: var(--white); }
  .origin__title {
    font-weight: 600; font-size: 12.5px; letter-spacing: .2px;
    padding-bottom: 2px; border-bottom: 1px solid var(--white); display: inline-block;
  }
  .origin__dist { font-weight: 500; font-size: 10.5px; line-height: 10px; margin-top: 4px; }
  .origin__cert { font-size: 7px; margin-top: 5px; }

  .front-panel {
    position: absolute; left: 366px; top: 7px; width: 371px; height: 156px;
    background: var(--white); padding: 4px;
  }
  .front-panel__inner {
    width: 100%; height: 100%; background: var(--matcha);
    display: flex; flex-direction: column; align-items: center; justify-content: flex-end;
    padding-bottom: 8px; color: var(--white); text-align: center;
  }
  .front-panel__brand { font-weight: 600; font-size: 18px; margin-bottom: 10px; }
  .front-panel__headline { font-weight: 700; font-size: 20px; line-height: 20px; letter-spacing: .2px; }
  .front-panel__sub { font-weight: 300; font-size: 15px; line-height: 17px; letter-spacing: .2px; }

  .net-weight {
    position: absolute; left: 0; width: 100%; top: 166px;
    text-align: center; font-size: 9px; color: var(--white);
  }

  .info { position: absolute; left: 906px; top: 9px; width: 180px; color: var(--ink); }
  .info__title { font-weight: 600; font-size: 9.5px; line-height: 10.5px; }
  .info__heading { font-weight: 600; font-size: 7.5px; margin-top: 8px; }
  .info__list { list-style: none; font-size: 6.8px; line-height: 10px; margin-top: 2px; }
  .info__list li::before { content: "• "; }

  .cert-badges { position: absolute; left: 906px; top: 107px; display: flex; gap: 17px; align-items: center; }
  .cert-badge--square { width: 73px; height: 56px; background: var(--badge-green); border: 2px solid var(--white); }
  .cert-badge--round {
    width: 62px; height: 62px; border-radius: 50%;
    background: var(--badge-green); border: 3px solid var(--white);
    box-shadow: 0 0 0 2px var(--badge-brown);
  }
</style>
</head>
<body>
<main class="canvas">
  <section class="label" aria-label="Kesso Tea matcha jar label">
    <div class="label__top"></div>

    <div class="brand-mark">
      <span class="brand-mark__dot"></span>
      <span>Kesso Tea</span>
    </div>

    <div class="origin">
      <p class="origin__title">PRODUCT OF JAPAN</p>
      <p class="origin__dist">Distributed by Kesso Tea Co.<br>Marlow, Ga</p>
      <p class="origin__cert">Certified Organic by orra</p>
    </div>

    <div class="front-panel">
      <div class="front-panel__inner">
        <p class="front-panel__brand">Kesso Tea</p>
        <p class="front-panel__headline">PREMIUM ORGANIC</p>
        <p class="front-panel__sub">CEREMONIAL MATCHA</p>
      </div>
    </div>

    <p class="net-weight">Net Wt: 30g</p>

    <div class="info">
      <p class="info__title">Premium Organic Japanese<br>Matcha Green Tea</p>
      <p class="info__heading">INSTRUCTIONS</p>
      <ul class="info__list">
        <li>2 tsp of Matcha</li>
        <li>2oz of Water (170-180 degrees F)</li>
        <li>Whisk in a W formation until frothy</li>
        <li>Sweeten to taste</li>
      </ul>
    </div>

    <div class="cert-badges">
      <div class="cert-badge--square" role="img" aria-label="Non-GMO verification badge"></div>
      <div class="cert-badge--round" role="img" aria-label="Organic certification seal"></div>
    </div>
  </section>
</main>
</body>
</html>
```